Professional Business Card - TWO SIDES

I need a new business card design to be used by myself and my employees. I would like a professional card and for the front I thought I would like a dark blue thatch with our logo in a raised gold foil on top of it. On the other side I would like name, position, and contact info. I've uploaded our old design for an example of the info used.

Target Market(s)

Business Clients

Industry/Entity Type

CPA Firm

Contact Information for Business Card

Logo, Name, Title, Address, Phone Numbers, Website address, Email Address

Font styles to use
Serif
Sans Serif

Colors
0054AA
0677BA
7BADD7
CADEEF
E8F1F8
0094D4
00A9DD
6FCCEA
C7EBF8
E9F6FB

Requirements
Must have
• Modern Professional Look
Nice to have
• Logo in Gold Foil or ability to have is raised. I like our logo in a single color
Should not have
• I've uploaded old business card

```html
<!DOCTYPE html>
<html lang="en">
<head>
<meta charset="utf-8">
<title>Hale &amp; Hale – Business Card</title>
<link rel="stylesheet" href="https://fonts.googleapis.com/css2?family=Arimo:wght@400;700&display=swap">
<style>
  :root {
    --page-bg: #e9e9e7;
    --card-navy: #06305f;
    --card-edge: #9cc51e;
    --accent-lime: #a8d026;
    --text-white: #ffffff;
    --rule-grey: #aab7c8;
    --mark-light: #3b7fc0;
    --mark-dark: #0a2747;
  }
  * { box-sizing: border-box; margin: 0; padding: 0; }
  html, body {
    width: 1200px; height: 801px; overflow: hidden;
    background: var(--page-bg);
    font-family: "Arimo", Arial, sans-serif;
  }
  .sheet {
    position: relative; width: 1200px; height: 801px;
    display: flex; align-items: center; justify-content: center; gap: 40px;
  }
  .card {
    position: relative; width: 540px; height: 309px;
    background: var(--card-navy);
    border-bottom: 4px solid var(--card-edge);
    border-right: 2px solid var(--card-edge);
    overflow: hidden;
    color: var(--text-white);
  }
  .wordmark { position: absolute; }
  .wordmark-name {
    display: flex; align-items: center; gap: 8px;
    font-weight: 700; font-size: 32px; letter-spacing: 1px;
    color: var(--text-white); line-height: 1;
  }
  .wordmark-dot {
    width: 12px; height: 12px; border-radius: 50%;
    background: var(--accent-lime); flex: none;
  }
  .wordmark-tagline {
    margin-top: 6px; font-weight: 700; font-size: 11.5px;
    letter-spacing: 2.4px; color: var(--text-white);
  }
  /* Info side */
  .card-info .wordmark { left: 34px; top: 122px; }
  .card-info .wordmark-name { font-size: 30px; }
  .card-info .wordmark-tagline { font-size: 10.5px; letter-spacing: 2.3px; }
  .divider {
    position: absolute; left: 292px; top: 60px; width: 1px; height: 190px;
    background: var(--rule-grey);
  }
  .contact { position: absolute; left: 318px; top: 58px; right: 12px; }
  .contact-name { font-size: 24px; font-weight: 700; color: var(--accent-lime); line-height: 1.1; }
  .contact-role { font-size: 15px; margin-top: 2px; }
  .contact-address { font-size: 15px; line-height: 1.3; margin-top: 14px; }
  .contact-list { list-style: none; margin-top: 16px; }
  .contact-list li {
    display: flex; align-items: center; gap: 9px;
    font-size: 15px; line-height: 1.45; white-space: nowrap;
  }
  .contact-list svg { width: 13px; height: 13px; flex: none; }
  /* Brand side */
  .mark-area {
    position: absolute; left: 0; top: 0; width: 230px; height: 309px;
    background: linear-gradient(160deg, var(--mark-dark) 0%, #16457a 45%, var(--mark-light) 100%);
    opacity: .85;
  }
  .card-brand .wordmark { right: 28px; bottom: 44px; }
</style>
</head>
<body>
<main class="sheet">
  <section class="card card-info" aria-label="Card back with contact details">
    <div class="wordmark">
      <div class="wordmark-name">HALE <span class="wordmark-dot"></span> HALE</div>
      <div class="wordmark-tagline">CERTIFIED PUBLIC ACCOUNTANTS</div>
    </div>
    <div class="divider"></div>
    <div class="contact">
      <p class="contact-name">Daniel Reyes</p>
      <p class="contact-role">Manager</p>
      <p class="contact-address">410 Elm Street, Dayton<br>Ohio, 45402</p>
      <ul class="contact-list">
        <li>
          <svg viewBox="0 0 16 16" aria-hidden="true"><path fill="#a8d026" d="M3.5 1.5l2.5 0 1 3.5-1.6 1.2c.8 1.7 2 2.9 3.7 3.7L10.3 8.3l3.5 1v2.5c0 .9-.8 1.7-1.7 1.6C6.6 13 2.9 9.3 2 3.3c-.1-.9.6-1.8 1.5-1.8z"/></svg>
          555-318-0427
        </li>
        <li>
          <svg viewBox="0 0 16 16" aria-hidden="true"><rect x="1.5" y="3.5" width="13" height="9" fill="none" stroke="#a8d026" stroke-width="1.6"/><path d="M1.5 3.5l6.5 5 6.5-5" fill="none" stroke="#a8d026" stroke-width="1.6"/></svg>
          info@halecpa-demo.com
        </li>
        <li>
          <svg viewBox="0 0 16 16" aria-hidden="true"><circle cx="8" cy="8" r="6.5" fill="#a8d026"/><path d="M1.5 8h13M8 1.5c-3 3.5-3 9.5 0 13M8 1.5c3 3.5 3 9.5 0 13" fill="none" stroke="#06305f" stroke-width="1"/></svg>
          www.halecpa-demo.com
        </li>
      </ul>
    </div>
  </section>

  <section class="card card-brand" aria-label="Card front with firm name">
    <div class="mark-area" role="img" aria-label="Large soft-blue brand motif area"></div>
    <div class="wordmark">
      <div class="wordmark-name">HALE <span class="wordmark-dot"></span> HALE</div>
      <div class="wordmark-tagline">CERTIFIED PUBLIC ACCOUNTANTS</div>
    </div>
  </section>
</main>
</body>
</html>
```